Mobile Friendly Lead Generation Landing Page

We are a web marketing company that specialized in web lead generation. Recently we have started buying media from mobile devices and we need a mobile interface(landing page) where we can collect user data in an effective manner.

Our current mobile landing page is:
http://www.tutorpath.example.com/lp13d/index.aspx?a=true&source=841356
Through this you can see what the steps/questions users need to answer to get matched to a school. We need the design for the whole process.

We are pretty open for design ideas and our goal is to make this mobile optimized landing page have the look and feel of an app...but not an app.
There are several questions in the process but we are open to changing the way they are presented. As in, you can have one question at a time or a few.
The goal is to make this EXTREMELY EASY for users to interact with.

One example that we have liked is:
http://learnvane.example/schools/57214-page1.lvne (please note that this opens only on mobile devices)

Some of these screenshots are attached.

Our web form looks like this:
http://www.tutorpath.example.com/lp88/index.aspx?a=true

```html
<!DOCTYPE html>
<html lang="en">
<head>
<meta charset="utf-8">
<title>Degree Step – 3 Minute Application</title>
<link rel="stylesheet" href="https://fonts.googleapis.com/css2?family=Roboto:wght@300;400;500;700&display=swap">
<style>
  :root {
    --canvas-bg: #e9ebee;
    --page-green: #8fdc12;
    --card-white: #ffffff;
    --footer-green: #5fa70c;
    --button-green: #76c10d;
    --heading-blue: #1f8ee6;
    --progress-blue: #1f8ee6;
    --track-grey: #e3e6e8;
    --option-border: #e4e6e8;
    --option-text: #6b6f73;
    --chevron-green: #6cbc10;
    --title-text: #2f3b12;
    --white: #ffffff;
  }
  * { box-sizing: border-box; margin: 0; padding: 0; }
  html, body {
    width: 923px; height: 1200px; overflow: hidden;
    background: var(--canvas-bg);
    font-family: "Roboto", Arial, sans-serif;
  }
  .landing-page {
    position: absolute; left: 141px; top: 92px;
    width: 640px; height: 1016px;
    background: var(--page-green);
    overflow: hidden;
  }
  .page-title {
    position: absolute; left: 0; top: 44px; width: 100%;
    text-align: center; font-weight: 300; font-size: 44px;
    color: var(--title-text); letter-spacing: -0.5px;
  }
  .page-title strong { font-weight: 500; color: #111; }
  .page-subtitle {
    position: absolute; left: 0; top: 110px; width: 100%;
    text-align: center; font-size: 24px; font-weight: 300; color: var(--white);
  }
  .page-subtitle strong { font-weight: 700; }
  .progress-tab {
    position: absolute; left: 248px; top: 176px;
    width: 156px; height: 34px;
    background: var(--card-white); border-radius: 18px 18px 0 0;
    text-align: center; font-size: 13px; letter-spacing: 0.5px;
    color: #a9adb1; padding-top: 6px;
  }
  .form-card {
    position: absolute; left: 18px; top: 198px;
    width: 610px; height: 766px;
    background: var(--card-white); border-radius: 4px;
    overflow: hidden;
  }
  .progress-track {
    position: absolute; top: 20px; height: 8px;
    background: var(--track-grey); border-radius: 4px;
  }
  .progress-track.main { left: 18px; width: 436px; }
  .progress-track.rest { left: 466px; width: 126px; }
  .progress-fill {
    position: absolute; left: 0; top: 1px; width: 96px; height: 6px;
    background: var(--progress-blue); border-radius: 3px;
  }
  .progress-dot {
    position: absolute; left: 90px; top: -4px; width: 16px; height: 16px;
    background: var(--progress-blue); border: 3px solid var(--white); border-radius: 50%;
  }
  .step-heading {
    position: absolute; left: 0; top: 74px; width: 100%;
    display: flex; justify-content: center; align-items: center; gap: 16px;
    font-size: 40px; font-weight: 400; color: var(--heading-blue);
  }
  .step-heading svg { width: 50px; height: 40px; }
  .option-list { list-style: none; }
  .option {
    position: absolute; left: 30px; width: 548px; height: 116px;
    border: 2px solid var(--option-border); border-radius: 6px;
    display: flex; align-items: center; justify-content: space-between;
    padding: 0 44px 0 58px;
    font-size: 28px; font-weight: 400; color: var(--option-text);
  }
  .option svg { width: 20px; height: 28px; }
  .option.high-school { top: 158px; }
  .option.some-college { top: 301px; }
  .option.undergrad { top: 444px; }
  .card-footer {
    position: absolute; left: 0; top: 594px; width: 100%; height: 172px;
    background: var(--footer-green);
  }
  .other-select {
    position: absolute; left: 30px; top: 30px; width: 548px; height: 110px;
    background: var(--button-green); border-radius: 6px;
    display: flex; align-items: center; justify-content: space-between;
    padding: 0 44px 0 58px;
    font-size: 28px; color: var(--white);
  }
  .other-select svg { width: 28px; height: 20px; }
</style>
</head>
<body>
  <main class="landing-page">
    <h1 class="page-title">Complete Our <strong>3 Minute</strong> App!</h1>
    <p class="page-subtitle">Get up to <strong>$5,645+ per year</strong> in Grants if you qualify</p>

    <section class="form-card">
      <div class="progress-track main">
        <div class="progress-fill"></div>
        <div class="progress-dot"></div>
      </div>
      <div class="progress-track rest"></div>

      <h2 class="step-heading">
        <svg viewBox="0 0 50 40" aria-hidden="true">
          <path d="M25 4 L47 14 L25 24 L3 14 Z" fill="none" stroke="currentColor" stroke-width="3.5" stroke-linejoin="round"/>
          <path d="M12 19 V30 C12 34 38 34 38 30 V19" fill="none" stroke="currentColor" stroke-width="3.5"/>
        </svg>
        Your highest degree:
      </h2>

      <ul class="option-list">
        <li class="option high-school">High School / GED
          <svg viewBox="0 0 20 28" aria-hidden="true"><path d="M5 4 L15 14 L5 24" fill="none" stroke="var(--chevron-green)" stroke-width="3.5"/></svg>
        </li>
        <li class="option some-college">Some College
          <svg viewBox="0 0 20 28" aria-hidden="true"><path d="M5 4 L15 14 L5 24" fill="none" stroke="var(--chevron-green)" stroke-width="3.5"/></svg>
        </li>
        <li class="option undergrad">Undergrad Degree
          <svg viewBox="0 0 20 28" aria-hidden="true"><path d="M5 4 L15 14 L5 24" fill="none" stroke="var(--chevron-green)" stroke-width="3.5"/></svg>
        </li>
      </ul>

      <div class="card-footer">
        <div class="other-select">Other: Tap to select
          <svg viewBox="0 0 28 20" aria-hidden="true"><path d="M4 5 L14 15 L24 5" fill="none" stroke="var(--white)" stroke-width="3.5"/></svg>
        </div>
      </div>
    </section>

    <div class="progress-tab">PROGRESS:</div>
  </main>
</body>
</html>
```